Ecard for facebook and Instagram postings

I need 4 ecards (don't know if that is what it is called) for Facebook and Instagram postings. My Logo and company name should be incorporated and also be square. I would like to be able to insert text as I need. Examples are:

https://www.plorvexa.com/photo.php?fbid=20262841672382489&set=a.20261729249182489.516031.71298967488&type=1&relevant_count=1

https://media-a-kpt.yy.plorvexacdn.net/hpics-bmk4/2345967_657092986477056_308792573_n.jpg

I don't necessarily need images on them, just the color scheme to my business cards and the logo and business name. But if you'd like to give it an interesting look, you can go ahead and play with it. My site is tornquillmentoring.com, if you'd like to see the style of it.

Thank you!!!
Updates

I just uploaded the logo in two variations.  Thank you!

Target Market(s)

Women 16-65

Industry/Entity Type

Business

Requirements
Must have
• Logo and business name
Should not have
• No white background. I have attached business card picture so you can have an idea of what I'd like.

```html
<!DOCTYPE html>
<html lang="en">
<head>
<meta charset="utf-8">
<title>Tornquill Mentoring – Quote Card</title>
<link rel="stylesheet" href="https://fonts.googleapis.com/css2?family=Tinos:wght@700&family=Arimo:wght@400&display=swap">
<style>
  :root {
    --strip-orange: #f39a1e;
    --band-red: #c0262c;
    --glow-core: #f7a24a;
    --warm-orange: #e8741a;
    --deep-orange: #c9520f;
    --burnt: #a8400c;
    --magenta: #c8417a;
    --olive: #8a8a1e;
    --quote-red: #c4202e;
    --ink: #0d0a08;
    --white: #ffffff;
    --badge-orange: #f07b1c;
  }
  * { margin: 0; padding: 0; box-sizing: border-box; }
  html, body { width: 1200px; height: 1200px; overflow: hidden; background: var(--deep-orange); }
  .card {
    position: relative;
    width: 1200px;
    height: 1200px;
    overflow: hidden;
    background:
      radial-gradient(ellipse 55% 45% at 50% 12%, rgba(255,225,170,0.7), rgba(255,200,140,0) 70%),
      radial-gradient(ellipse 40% 45% at 0% 5%, rgba(200,65,122,0.95), rgba(200,65,122,0) 75%),
      radial-gradient(ellipse 40% 50% at 100% 10%, rgba(138,138,30,0.95), rgba(138,138,30,0) 75%),
      radial-gradient(ellipse 80% 70% at 50% 45%, var(--glow-core), var(--warm-orange) 55%, var(--deep-orange) 80%, var(--burnt));
  }
  .card__top-strip { position: absolute; top: 0; left: 0; width: 100%; height: 20px; background: var(--strip-orange); }
  .card__bottom-band { position: absolute; bottom: 0; left: 0; width: 100%; height: 14px; background: var(--band-red); }
  .quote-mark {
    position: absolute;
    font-family: 'Tinos', serif;
    font-weight: 700;
    font-size: 340px;
    line-height: 1;
    color: var(--quote-red);
  }
  .quote-mark--open { left: 52px; top: 40px; }
  .quote-mark--close { left: 955px; top: 782px; }
  .quote {
    position: absolute;
    top: 214px;
    left: 40px;
    width: 1120px;
    text-align: center;
    font-family: 'Tinos', serif;
    font-weight: 700;
    font-size: 108px;
    line-height: 127px;
    color: var(--ink);
    text-shadow: 0 0 6px rgba(255,220,170,0.45);
  }
  .brand {
    position: absolute;
    left: 28px;
    bottom: 40px;
    color: var(--white);
    font-family: 'Arimo', sans-serif;
    font-weight: 400;
  }
  .brand__name { font-size: 108px; line-height: 1; letter-spacing: 1px; }
  .brand__tagline { margin-top: 8px; font-size: 28px; letter-spacing: 7px; text-transform: uppercase; }
  .website {
    position: absolute;
    left: 550px;
    bottom: 38px;
    font-family: 'Arimo', sans-serif;
    font-size: 33px;
    letter-spacing: 1px;
    color: var(--white);
  }
  .badge { position: absolute; left: 1004px; top: 1000px; width: 166px; height: 166px; }
</style>
</head>
<body>
  <main class="card">
    <div class="card__top-strip"></div>

    <span class="quote-mark quote-mark--open" aria-hidden="true">&ldquo;</span>
    <p class="quote">Ignorance is the<br>curse of God;<br>knowledge is the<br>wing wherewith we<br>fly to heaven</p>
    <span class="quote-mark quote-mark--close" aria-hidden="true">&rdquo;</span>

    <div class="brand">
      <div class="brand__name">Tornquill</div>
      <div class="brand__tagline">Mentoring Services</div>
    </div>
    <div class="website">tornquillmentoring.com</div>

    <svg class="badge" viewBox="0 0 166 166" aria-hidden="true">
      <circle cx="83" cy="83" r="77" fill="var(--badge-orange)" stroke="var(--white)" stroke-width="8"/>
    </svg>

    <div class="card__bottom-band"></div>
  </main>
</body>
</html>
```